Boutique custom software development company needs new business card

Our nearly 20 year old custom software development company would like to better include the fact that we are now providing Bitcoin services. These new services are B2B include education (how to acquire and securely hold Bitcoin) and integrating Bitcoin payments into existing ecommerce sites or other existing systems. Please keep the card clean and simple. Attached is our current design and some other files. vextorial.com

Target Market(s)

businesses owners interested in long term relationship

Industry/Entity Type

Custom software development and Bitcoin

Contact Information for Business Card

Dale Parker, dale@vextorial.com, vextorial.com, (888) 555-VXTRL

Font styles to use
Other font styles liked:
• monospace

Requirements
Must have
• double-sided
Nice to have
• clean and simple
Should not have
• physical address

```html
<!DOCTYPE html>
<html lang="en">
<head>
<meta charset="utf-8">
<title>Vextorial Business Card</title>
<link href="https://fonts.googleapis.com/css2?family=Montserrat:wght@600;700&family=Open+Sans:wght@400&display=swap" rel="stylesheet">
<style>
  :root {
    --stage: #8a8a88;
    --card-white: #ffffff;
    --card-black: #121212;
    --brand-blue: #3f72b8;
    --brand-orange: #ee7623;
    --text-grey: #555555;
    --edge-blue: #2f63c4;
  }
  html, body {
    margin: 0;
    padding: 0;
    width: 1200px;
    height: 801px;
    overflow: hidden;
    background: var(--stage);
  }
  .stage {
    position: relative;
    width: 1200px;
    height: 801px;
    display: flex;
    align-items: center;
    justify-content: center;
    gap: 60px;
  }
  .card {
    position: relative;
    width: 500px;
    height: 286px;
    box-sizing: border-box;
    border-bottom: 2px solid var(--edge-blue);
    box-shadow: 0 6px 18px rgba(0,0,0,0.25);
  }
  .card-front {
    background: var(--card-white);
    display: flex;
    align-items: center;
    padding: 0 28px 0 36px;
  }
  .brand-block {
    flex: none;
    width: 236px;
  }
  .brand-name {
    display: flex;
    align-items: center;
    gap: 8px;
    font-family: "Montserrat", sans-serif;
    font-weight: 700;
    font-size: 28px;
    letter-spacing: -0.5px;
    color: var(--brand-blue);
    line-height: 1;
    white-space: nowrap;
  }
  .brand-square {
    width: 16px;
    height: 16px;
    background: var(--brand-orange);
    flex: none;
  }
  .tagline {
    margin-top: 7px;
    font-family: "Open Sans", sans-serif;
    font-size: 12px;
    color: var(--brand-blue);
    white-space: nowrap;
  }
  .divider {
    flex: none;
    width: 1px;
    height: 72px;
    background: var(--brand-blue);
    margin: 0 20px 0 0;
  }
  .contact-block {
    flex: 1;
    min-width: 0;
  }
  .person-name {
    font-family: "Montserrat", sans-serif;
    font-weight: 700;
    font-size: 16px;
    color: var(--brand-blue);
    text-transform: uppercase;
    margin-bottom: 8px;
    white-space: nowrap;
  }
  .contact-list {
    list-style: none;
    margin: 0;
    padding: 0;
    font-family: "Open Sans", sans-serif;
    font-size: 12.5px;
    color: var(--text-grey);
  }
  .contact-list li {
    display: flex;
    align-items: center;
    gap: 7px;
    line-height: 20px;
    white-space: nowrap;
  }
  .contact-icon {
    width: 10px;
    height: 10px;
    fill: var(--brand-orange);
    flex: none;
  }
  .card-back {
    background: var(--card-black);
    display: flex;
    align-items: center;
    justify-content: center;
  }
  .back-mark {
    display: flex;
    align-items: center;
    gap: 10px;
    font-family: "Montserrat", sans-serif;
    font-weight: 700;
    font-size: 40px;
    color: var(--brand-blue);
  }
  .back-mark .brand-square {
    width: 22px;
    height: 22px;
  }
</style>
</head>
<body>
<main class="stage">
  <section class="card card-front">
    <div class="brand-block">
      <div class="brand-name"><span class="brand-square"></span>VEXTORIAL</div>
      <div class="tagline">custom applications &amp; bitcoin services</div>
    </div>
    <div class="divider"></div>
    <div class="contact-block">
      <div class="person-name">Dale Parker</div>
      <ul class="contact-list">
        <li>
          <svg class="contact-icon" viewBox="0 0 10 10" aria-hidden="true"><path d="M2 0.5 L3.6 2.6 L2.6 3.6 Q3.6 5.8 6.4 7.4 L7.4 6.4 L9.5 8 L8.2 9.5 Q3 8.6 0.5 1.8 Z"/></svg>
          (888) 555-VXTRL
        </li>
        <li>
          <svg class="contact-icon" viewBox="0 0 10 10" aria-hidden="true"><path d="M0 2 H10 V8.5 H0 Z M0 2 L5 5.8 L10 2" stroke="#fff" stroke-width="0.8"/></svg>
          dale@vextorial.com
        </li>
        <li>
          <svg class="contact-icon" viewBox="0 0 10 10" aria-hidden="true"><circle cx="5" cy="5" r="4.6"/><path d="M0.6 5 H9.4 M5 0.6 Q2.4 5 5 9.4 M5 0.6 Q7.6 5 5 9.4" stroke="#fff" stroke-width="0.7" fill="none"/></svg>
          www.vextorial.com
        </li>
      </ul>
    </div>
  </section>

  <section class="card card-back">
    <div class="back-mark"><span class="brand-square"></span>VEXTORIAL</div>
  </section>
</main>
</body>
</html>
```